I need a SEO-friendly Wordpress website (making sure to style H1, H2, H3, etc correctly) for a Hawaii-based law firm called Meridian Crest Legal Group. Comparable websites include https://brvlaw.example/ and https://www.lomrit.example/ for design reference. The current copy on the TarnAdvocate.example website can be used.

```html
<!DOCTYPE html>
<html lang="en">
<head>
<meta charset="utf-8">
<title>Meridian Crest Legal Group</title>
<link href="https://fonts.googleapis.com/css2?family=Roboto:wght@400;500;700&family=Lato:wght@400;700&family=Roboto+Condensed:wght@700&family=Tinos:wght@700&display=swap" rel="stylesheet">
<style>
:root{
  --orange:#b0600f;
  --orange-dark:#7d3408;
  --rust:#8a3a0c;
  --ink:#111;
  --black:#050505;
  --text:#666;
  --white:#fff;
  --footer:#1b1a19;
}
*{box-sizing:border-box;margin:0;padding:0}
html,body{width:1200px;height:3405px;overflow:hidden}
body{position:relative;font-family:"Lato",sans-serif;color:var(--ink);background:var(--white)}
.abs{position:absolute}
h1,h2,h3,h4{font-family:"Roboto",sans-serif;font-weight:700}
.topbar{left:0;top:0;width:1200px;height:45px;background:var(--black);color:var(--white);font-size:13px}
.topbar .item{position:absolute;top:11px;display:flex;align-items:center;gap:12px}
.ico{width:28px;height:28px;border-radius:50%;background:var(--orange);display:flex;align-items:center;justify-content:center}
.navbar{left:0;top:45px;width:1200px;height:44px;background:var(--orange)}
.brand{position:absolute;left:163px;top:8px;font-family:"Tinos",serif;font-weight:700;font-size:23px;color:var(--white)}
.menu{position:absolute;right:163px;top:9px;display:flex;gap:4px;list-style:none}
.menu li{font-size:12px;color:var(--white);padding:6px 10px;font-family:"Lato",sans-serif}
.menu li.active{background:var(--orange-dark)}
.hero{left:0;top:89px;width:1200px;height:601px;background:linear-gradient(100deg,#5e5a52 0%,#8a8270 30%,#c9b48a 55%,#7a6a52 80%,#3d342a 100%)}
.hero-panel{left:600px;top:221px;width:600px;height:337px;background:rgba(40,40,38,.88);text-align:right;padding-right:163px}
.eyebrow{margin-top:54px;color:var(--orange);font-family:"Roboto",sans-serif;font-weight:700;font-size:21px;letter-spacing:3px}
.hero h1{margin-top:14px;color:var(--white);font-size:52px;line-height:60px;font-weight:500}
.about{left:0;top:690px;width:1200px;height:412px}
.about-copy{left:0;top:0;width:600px;height:412px;background:linear-gradient(90deg,#823409,#b0600f);color:var(--white);padding:42px 30px 0 163px}
.about-copy h2{font-size:38px;font-weight:500;margin-bottom:22px;color:var(--ink)}
.about-copy p{font-size:12px;line-height:19.6px;margin-bottom:18px}
.btn-light{display:inline-block;background:var(--white);color:var(--ink);font-family:"Roboto",sans-serif;font-weight:700;font-size:14px;padding:10px 16px;outline:2px solid var(--white);outline-offset:2px;border:1px solid var(--orange)}
.about-media{left:600px;top:0;width:600px;height:412px;background:linear-gradient(120deg,#3a3a3c,#5c5a56 45%,#2a2624)}
.play{position:absolute;left:275px;top:182px;width:48px;height:48px;border-radius:50%;background:var(--orange);display:flex;align-items:center;justify-content:center}
.section-title{left:0;width:1200px;text-align:center;font-size:36px;font-weight:500}
.card{top:1278px;width:202px;height:337px;background:var(--white);box-shadow:0 2px 8px rgba(0,0,0,.15);text-align:center}
.card .photo{height:150px}
.card h3{font-size:16px;font-weight:500;margin:27px 0 8px}
.card p{font-size:11px;line-height:19.6px;color:var(--text);padding:0 12px;height:62px}
.btn{display:inline-block;margin-top:14px;background:var(--orange);color:var(--white);font-family:"Roboto",sans-serif;font-weight:700;font-size:11.5px;padding:11px 15px;outline:1px solid var(--orange);outline-offset:2px}
.timeline{left:599px;top:1817px;width:2px;height:369px;background:var(--orange)}
.dot{position:absolute;width:14px;height:14px;border-radius:50%;background:var(--orange-dark);left:593px}
.ring{position:absolute;width:14px;height:14px;border-radius:50%;border:2px solid var(--orange);background:var(--white);left:593px}
.ring::after{content:"";position:absolute;left:3px;top:3px;width:4px;height:4px;border-radius:50%;background:var(--orange)}
.attorney h4{font-size:17px;font-weight:500;margin-bottom:8px}
.attorney p{font-size:11px;line-height:19.6px;color:var(--text)}
.more{display:inline-block;margin-top:8px;font-family:"Roboto Condensed",sans-serif;font-size:12px;color:var(--orange)}
.blog-frame{left:147px;top:2392px;width:186px;height:262px;background:var(--orange)}
.blog-photo{left:161px;top:2411px;width:427px;height:224px;background:linear-gradient(110deg,#2e3a48,#7a8696 45%,#c9ccd0 65%,#4a4f58)}
.blog-copy{left:628px;top:2412px;width:392px}
.blog-copy h3{font-size:16px;font-weight:500;margin-bottom:6px}
.blog-copy p{font-size:11px;line-height:19.6px;color:var(--text)}
.arrow{width:30px;height:30px;border-radius:50%;background:var(--orange);display:flex;align-items:center;justify-content:center;outline:2px solid var(--orange);outline-offset:2px}
.cta{left:0;top:2741px;width:1200px;height:111px;background:var(--orange)}
.cta h2{position:absolute;left:163px;top:26px;color:var(--white);font-size:29px;line-height:41px;font-weight:500}
.cta .btn-light{position:absolute;left:928px;top:43px;padding:9px 16px}
.footer{left:0;top:2852px;width:1200px;height:505px;background:var(--footer);color:var(--white)}
.footer h3{position:absolute;top:75px;color:var(--orange);font-size:22px;font-weight:500}
.info{position:absolute;left:160px;display:flex;align-items:center;gap:40px;font-size:11.5px;line-height:19px}
.info .circle{width:46px;height:46px;border-radius:50%;border:2px solid var(--orange);display:flex;align-items:center;justify-content:center;flex:none}
.follow{position:absolute;left:163px;top:380px;font-family:"Roboto",sans-serif;font-weight:700;font-size:14px}
.social{position:absolute;top:366px;width:46px;height:46px;border-radius:50%}
.field{position:absolute;left:611px;width:428px;background:var(--white);border-radius:3px;color:#555;font-size:11px;padding:13px 16px}
.submit{position:absolute;left:612px;top:402px;background:var(--orange);color:var(--white);font-family:"Roboto",sans-serif;font-weight:700;font-size:11px;padding:11px 12px;outline:1px solid var(--orange);outline-offset:2px}
.copyright{left:0;top:3357px;width:1200px;height:48px;background:var(--orange);color:var(--white);font-size:11px;text-align:center;line-height:48px}
</style>
</head>
<body>

<header>
  <div class="abs topbar">
    <div class="item" style="left:160px"><span class="ico"><svg width="14" height="10" viewBox="0 0 14 10"><rect x="0.5" y="0.5" width="13" height="9" fill="none" stroke="#fff"/><path d="M1 1l6 5 6-5" fill="none" stroke="#fff"/></svg></span>hello@tarnadvocate.example</div>
    <div class="item" style="left:889px"><span class="ico"><svg width="14" height="14" viewBox="0 0 24 24"><path fill="#fff" d="M6.6 10.8a15 15 0 006.6 6.6l2.2-2.2a1 1 0 011-.25 11.4 11.4 0 003.6.57 1 1 0 011 1V20a1 1 0 01-1 1A17 17 0 013 4a1 1 0 011-1h3.5a1 1 0 011 1c0 1.25.2 2.45.57 3.6a1 1 0 01-.25 1z"/></svg></span>+1.808.555.0142</div>
  </div>
  <nav class="abs navbar">
    <div class="brand">Meridian Crest Legal Group</div>
    <ul class="menu">
      <li>Home</li><li class="active">Practice Area</li><li>Attorneys</li><li>Blog</li><li>Contact Us</li>
    </ul>
  </nav>
</header>

<section class="abs hero" role="img" aria-label="Statue of Lady Justice holding scales in a law library"></section>
<div class="abs hero-panel">
  <p class="eyebrow">WE ARE UNIQUE LAW FIRM</p>
  <h1>Personal Injury<br>Family &amp; Divorce<br>Child Custody</h1>
</div>

<section class="abs about">
  <div class="abs about-copy">
    <h2>About us</h2>
    <p>The experienced attorneys in the Meridian Crest Legal Group’s Kailua Kona, Hawaii office provide clients with a wide range of litigation expertise, including legal claims involving divorce &amp; family, personal injury, toxic exposures, intellectual property, and real estate.</p>
    <p>Our Kona office also offers commercial and hospitality litigation expertise on behalf of a wide variety of clients, including restaurants, hotels, property owners, and many others. We never wish to see our clients go to court, though if there is no other option, you’re in safe hands with our seasoned trial lawyers and the many years of courtroom experience behind them.</p>
    <span class="btn-light">Read More</span>
  </div>
  <div class="abs about-media" role="img" aria-label="Video still of a handshake over a desk with brass scales">
    <span class="play"><svg width="12" height="12" viewBox="0 0 12 12"><path d="M3 1l7 5-7 5z" fill="#fff"/></svg></span>
  </div>
</section>

<section>
  <h2 class="abs section-title" style="top:1174px">Practice Areas</h2>
  <article class="abs card" style="left:161px"><div class="photo" role="img" aria-label="Family walking together in a park" style="background:linear-gradient(160deg,#5d7a3a,#c9d2a8 60%,#8a9462)"></div><h3>Family &amp; Divorce</h3><p>Our lawyers handle all aspects of family law on the Big Island and neighboring islands...</p><span class="btn">Read More</span></article>
  <article class="abs card" style="left:386px"><div class="photo" role="img" aria-label="Bandaged arm resting on a hospital bed" style="background:linear-gradient(150deg,#c7a48c,#efe9e6 55%,#d6c9c2)"></div><h3>Personal Injury</h3><p>Dealing with personal injury and wrongful death claims is hard enough,...</p><span class="btn">Read More</span></article>
  <article class="abs card" style="left:611px"><div class="photo" role="img" aria-label="Business people shaking hands in an office" style="background:linear-gradient(120deg,#3a3c42,#c8ccd2 50%,#50545c)"></div><h3>Corporate &amp; IP</h3><p>The attorneys at MCLG have been helping Big Island business owners with all their legal needs...</p><span class="btn">Read More</span></article>
  <article class="abs card" style="left:835px"><div class="photo" role="img" aria-label="People reviewing documents at a wooden desk" style="background:linear-gradient(140deg,#6b4a2e,#b89470 50%,#e2d8cc)"></div><h3>Real Estate</h3><p>Our lawyers work with home owners, buyers and property developers to ensure...</p><span class="btn">Read More</span></article>
</section>

<section>
  <h2 class="abs section-title" style="top:1696px">Our Attorneys</h2>
  <div class="abs timeline"></div>
  <span class="dot" style="top:1810px"></span>
  <span class="ring" style="top:1929px"></span>
  <span class="ring" style="top:2050px"></span>
  <span class="dot" style="top:2179px"></span>
  <article class="abs attorney" style="left:170px;top:1868px;width:393px;text-align:right">
    <h4>DANIEL KEALOHA, ESQ.</h4>
    <p>The experienced attorneys in the Meridian Crest Legal Group’s Kailua Kona, Hawaii office provide clients with a wide range of litigation expertise, including legal claims involving divorce &amp; family, toxic exposures, intellectual property, and real estate.</p>
    <span class="more">Read More &#187;</span>
  </article>
  <article class="abs attorney" style="left:642px;top:1988px;width:390px">
    <h4>OWEN MARCHETTI, ESQ.</h4>
    <p>Owen Marchetti graduated from the Pacific Coast College of Law, in 1971. He has over 35 years of experience as a litigator in both State and Federal courts, primarily as a personal injury lawyer with experience as both a defense and plaintiff’s counsel.</p>
    <span class="more">Read More &#187;</span>
  </article>
</section>

<section>
  <h2 class="abs section-title" style="top:2274px">Our Blog</h2>
  <div class="abs blog-frame"></div>
  <div class="abs blog-photo" role="img" aria-label="Colleagues meeting around a table with a tablet"></div>
  <article class="abs blog-copy">
    <h3>Top 10 Things to Do Before Filing for Divorce</h3>
    <p>No one gets married with the intention of things not working out, but it’s an unfortunate fact that many marriages don’t work out in the end. For those who are in troubled marriage, here are the Top 10 things you should do before filing for a divorce. And whether you’re a client or not, from all of us here at Meridian Crest Legal Group, we hope that this checklist can help you through tough times.</p>
    <span class="btn" style="margin-top:40px">Read More</span>
  </article>
  <span class="abs arrow" style="left:48px;top:2508px"><svg width="16" height="16" viewBox="0 0 16 16"><path d="M13 8H3M7 4L3 8l4 4" stroke="#fff" stroke-width="2" fill="none"/></svg></span>
  <span class="abs arrow" style="left:1112px;top:2508px"><svg width="16" height="16" viewBox="0 0 16 16"><path d="M3 8h10M9 4l4 4-4 4" stroke="#fff" stroke-width="2" fill="none"/></svg></span>
</section>

<section class="abs cta">
  <h2>Dedicated to making sure you receive the care<br>and attention you need</h2>
  <span class="btn-light">Contact Us</span>
</section>

<footer class="abs footer">
  <h3 style="left:163px">Our Info</h3>
  <div class="info" style="top:135px"><span class="circle"><svg width="18" height="18" viewBox="0 0 24 24"><path fill="#b0600f" d="M6.6 10.8a15 15 0 006.6 6.6l2.2-2.2a1 1 0 011-.25 11.4 11.4 0 003.6.57 1 1 0 011 1V20a1 1 0 01-1 1A17 17 0 013 4a1 1 0 011-1h3.5a1 1 0 011 1c0 1.25.2 2.45.57 3.6a1 1 0 01-.25 1z"/></svg></span>+1.808.555.0142</div>
  <div class="info" style="top:208px"><span class="circle"><svg width="18" height="13" viewBox="0 0 14 10"><rect x="0.5" y="0.5" width="13" height="9" fill="none" stroke="#b0600f"/><path d="M1 1l6 5 6-5" fill="none" stroke="#b0600f"/></svg></span>hello@tarnadvocate.example</div>
  <div class="info" style="top:281px"><span class="circle"><svg width="16" height="20" viewBox="0 0 16 20"><path d="M8 0a7 7 0 017 7c0 5-7 13-7 13S1 12 1 7a7 7 0 017-7z" fill="#b0600f"/><circle cx="8" cy="7" r="2.5" fill="#1b1a19"/></svg></span>48-210 Pali Lani Road, Suite 12, Kailua Kona,<br>Hawaii 96740.</div>
  <p class="follow">Follow Us On:</p>
  <span class="social" role="img" aria-label="Social profile" style="left:302px;background:#4b67a8"></span>
  <span class="social" role="img" aria-label="Social profile" style="left:363px;background:#d9231c"></span>
  <span class="social" role="img" aria-label="Social profile" style="left:422px;background:#24466b"></span>
  <span class="social" role="img" aria-label="Social profile" style="left:482px;background:#4cb3e8"></span>

  <h3 style="left:612px">Quick Message</h3>
  <div class="field" style="top:144px;height:44px">Name:</div>
  <div class="field" style="top:205px;height:43px">Phone:</div>
  <div class="field" style="top:264px;height:89px">Message:</div>
  <span class="submit">Submit Now</span>
</footer>

<div class="abs copyright">Copyrights 2019 © Meridian Crest Legal Group. All Rights Reserved. Terms &amp; Conditions | Privacy Policy</div>

</body>
</html>
```